Professional Personal Website with Blog and four sections

I am seeking a website design for myself. I would like the site to contain a blog, related to Information Security and several sections.

I am an established Information Security Consultant (one aspect of the site).
I am an author of a children's spiritual book that is "new thought" (another aspect of the site)
I am a co-founder of a secure social platform for kids and families (www.bramlowt.com)
I may want a section on finance as well, not sure at this moment

I want this site to be a personal website, not a subscription service or professional services sales site, I want the site to look very professional, so that I can share it with all types of people without concern - business, spiritual, other.

I have provided a photo of myself for the site, smart casual on a beach. The site will be hosted on dorianhelpe.com

You can see samples of what I am referring to by searching "personal website" on images.zentrova.com

I would like the page layout, and the images chopped up as individual jpgs, including hover images for buttons. I can do the coding

I would like the following buttons
Home, About, Information Security Blog, Passion Projects, Contact

I would like the top portion of the page to say "Tobin Marsh"
I would like the subtext to say:
Executive Information Security Architect, Author, and Idea Man

I envision the following

Target Market(s)

Executive / Technical / Creative types / Spritual types

Number of Pages Required

4 page

Requirements
Must have
• Blog section
Should not have
• No Matrix themes or No Cop themes, No Fingerprints or Eyeball scans

```html
<!DOCTYPE html>
<html lang="en">
<head>
<meta charset="utf-8">
<title>Tobin Marsh</title>
<link rel="stylesheet" href="https://fonts.googleapis.com/css2?family=Open+Sans:wght@300;400;600;700&family=Raleway:wght@300;400;700&display=swap">
<style>
:root{
  --ink:#222;
  --muted:#8a8a8a;
  --soft:#b5b5b5;
  --line:#d6d6d6;
  --white:#fff;
  --band:rgba(18,18,18,.82);
  --panel:#f7f7f7;
  --grey:#ececec;
  --button:#3a3a3a;
}
*{box-sizing:border-box;margin:0;padding:0}
html,body{width:1200px;height:3156px;overflow:hidden;background:var(--white)}
body{font-family:"Open Sans",Arial,sans-serif;color:var(--ink)}
.hero{position:relative;height:608px;background:linear-gradient(120deg,#2b2b2b 0%,#6b6b6b 40%,#9a9a9a 55%,#3d3d3d 80%,#1c1c1c 100%)}
.brand{position:absolute;left:96px;top:56px;color:var(--white);font-weight:700;font-size:26px;letter-spacing:1px}
.menu{position:absolute;right:90px;top:56px;color:var(--white);font-weight:600;font-size:24px;display:flex;align-items:center;gap:12px}
.menu-bars{display:flex;flex-direction:column;gap:4px}
.menu-bars span{display:block;width:22px;height:3px;background:var(--white)}
.hero-band{position:absolute;left:20px;right:0;top:340px;height:140px;background:var(--band);display:flex;align-items:center;padding-left:80px}
.hero-band p{color:var(--white);font-weight:700;font-size:24px;line-height:44px;text-transform:uppercase;letter-spacing:.5px}
.dots{position:absolute;left:576px;top:542px;display:flex;gap:10px}
.dots span{width:12px;height:12px;border:2px solid var(--white);border-radius:50%}
.dots span:first-child{background:var(--white)}

.intro{height:220px;text-align:center;padding-top:60px}
.intro h2{font-size:24px;font-weight:700;letter-spacing:1px}
.intro p{width:760px;margin:26px auto 0;font-size:13px;line-height:22px;color:var(--muted)}

.feature{position:relative;height:432px;display:flex}
.feature .copy{width:600px;background:var(--panel);padding:110px 0 0 100px}
.feature.reverse .copy{padding-left:100px}
.feature .photo{width:600px;height:432px}
.copy h3{font-family:"Raleway",sans-serif;font-weight:300;font-size:30px;line-height:44px;color:#666;text-transform:uppercase}
.copy h3 strong{font-family:"Open Sans",sans-serif;font-weight:700;color:var(--ink);font-size:27px}
.copy p{margin-top:14px;width:330px;font-size:13px;line-height:22px;color:var(--muted)}
.read-more{display:inline-block;margin-top:22px;padding:8px 20px;border:1px solid var(--line);border-radius:20px;font-size:11px;font-weight:700;color:var(--ink);text-transform:uppercase}

.photo-data{background:linear-gradient(135deg,#3a3f47 0%,#8a929c 45%,#d8dde2 70%,#5a626c 100%)}
.photo-book{background:linear-gradient(180deg,#6b4a2c 0%,#a37a52 40%,#e8e2d6 60%,#8a623c 100%)}
.photo-chart{background:linear-gradient(135deg,#9eb1c4 0%,#d9e1ea 40%,#5d7a99 70%,#c8c8c8 100%)}

.banner{position:relative;height:428px;background:linear-gradient(180deg,#3a3a3a 0%,#7a7a7a 45%,#4a4a4a 100%)}
.banner .mark{position:absolute;right:120px;top:222px;text-align:center;color:var(--white);font-size:11px;font-weight:600}
.banner .mark span{display:block;width:34px;height:34px;border-radius:50%;background:var(--white);margin:0 auto 4px}
.banner h3{position:absolute;right:120px;top:300px;text-align:right;font-family:"Raleway",sans-serif;font-weight:300;font-size:28px;line-height:40px;color:var(--white);text-transform:uppercase}
.banner h3 strong{font-family:"Open Sans",sans-serif;font-weight:700;font-size:26px}

.signup{height:168px;background:var(--grey);display:flex;align-items:center;justify-content:center;gap:40px}
.signup .field{width:380px;border-bottom:2px solid #555;padding:6px 0;font-size:13px;color:var(--muted);letter-spacing:1px}
.signup .submit{background:var(--button);color:var(--white);font-size:11px;font-weight:700;padding:10px 34px;border-radius:20px}

.news{height:340px;padding:56px 0 0 100px}
.news h2{font-size:28px;font-weight:700;letter-spacing:.5px}
.news-list{display:flex;gap:100px;margin-top:50px}
.post{display:flex;gap:26px;width:420px}
.post .thumb{width:96px;height:92px;flex:none;background:linear-gradient(180deg,#c9ced4 0%,#7d8690 100%)}
.post h4{font-size:15px;font-weight:600;color:#4a6a8a}
.post p{margin-top:8px;font-size:12px;line-height:20px;color:var(--muted)}
.post .meta{margin-top:8px;font-size:10px;color:var(--soft);display:flex;gap:40px}
.all-news{display:block;width:104px;margin:40px 0 0 450px;text-align:center;border:1px solid var(--line);border-radius:20px;padding:8px 0;font-size:10px;font-weight:700}

.footer{height:96px;background:var(--grey);text-align:center;padding-top:26px}
.footer .social{display:flex;justify-content:center;gap:14px}
.footer .social span{width:10px;height:10px;border-radius:50%;background:#555}
.footer p{margin-top:14px;font-size:11px;color:var(--muted)}
</style>
</head>
<body>
<header class="hero" role="img" aria-label="Hands holding a tablet with floating screens in the background">
  <div class="brand">TOBINMARSH</div>
  <div class="menu">MENU <div class="menu-bars"><span></span><span></span><span></span></div></div>
  <div class="hero-band"><p>We'll focus on areas where your application is most at risk, report back<br>issues found, and provide remediation advice.</p></div>
  <div class="dots"><span></span><span></span><span></span></div>
</header>

<section class="intro">
  <h2>WHAT WE DO</h2>
  <p>Security reviews, writing and platform work shaped by years of practice and a clear focus on people. Each project starts with listening, then moves to careful design and honest advice.</p>
</section>

<section class="feature">
  <div class="copy">
    <h3>Established<br><strong>Information Security Consultant</strong></h3>
    <p>Lorem ipsum is simply dummy text of the printing and type setting industry.</p>
    <span class="read-more">Read more</span>
  </div>
  <div class="photo photo-data" role="img" aria-label="Hand touching glowing data bar chart"></div>
</section>

<section class="feature reverse">
  <div class="photo photo-book" role="img" aria-label="Open book on a wooden table"></div>
  <div class="copy">
    <h3>Children's spiritual<br>book that is<br><strong>New Thought</strong></h3>
    <p>Lorem ipsum is simply dummy text of the printing and type setting industry.</p>
    <span class="read-more">Read more</span>
  </div>
</section>

<section class="banner" role="img" aria-label="Close black and white portrait of a child">
  <div class="mark"><span></span>BRAMLOWT</div>
  <h3>Co-founder of a secure social platform for<br><strong>Kids and Families</strong></h3>
</section>

<section class="feature">
  <div class="copy">
    <h3>Full protect for<br><strong>Financial</strong></h3>
    <p>Lorem ipsum is simply dummy text of the printing and type setting industry.</p>
    <span class="read-more">Read more</span>
  </div>
  <div class="photo photo-chart" role="img" aria-label="Business people reviewing charts on a tablet"></div>
</section>

<section class="signup">
  <div class="field">ENTER YOUR MAIL....</div>
  <span class="submit">SUBMIT</span>
</section>

<section class="news">
  <h2>LATEST NEWS</h2>
  <div class="news-list">
    <article class="post">
      <div class="thumb" role="img" aria-label="Portrait photo of the author"></div>
      <div>
        <h4>Contrary to popular belief</h4>
        <p>Lorem ipsum is simply dummy text of the printing and typesetting industry. Lorem ipsum has been.</p>
        <div class="meta"><span>May 2015</span><span>Security</span></div>
      </div>
    </article>
    <article class="post">
      <div class="thumb" role="img" aria-label="Portrait photo of the author"></div>
      <div>
        <h4>Contrary to popular belief</h4>
        <p>Lorem ipsum is simply dummy text of the printing and typesetting industry. Lorem ipsum has been.</p>
        <div class="meta"><span>May 2015</span><span>Security</span></div>
      </div>
    </article>
  </div>
  <span class="all-news">ALL NEWS</span>
</section>

<footer class="footer">
  <div class="social"><span></span><span></span><span></span><span></span></div>
  <p>© 2015 dorianhelpe.com. All rights reserved.</p>
</footer>
</body>
</html>
```